New Business Card Design Project

Use the flyer uploaded and website www.brightoakbuilders.com for inspiration.
List Our Services on Backside of business cards
Marcus Delling
Harborline Builders Inc.
Licensed General Contractors
858-471-6093

Contact Information for Business Card

Use the flyer uploaded and website www.brightoakbuilders.com for inspiration. List Our Services on Backside of business cards Marcus Delling Harborline Builders Inc. Licensed General Contractors 858-471-6093

```html
<!DOCTYPE html>
<html lang="en">
<head>
<meta charset="utf-8">
<title>Harborline Builders Inc. – Business Card</title>
<link rel="stylesheet" href="https://fonts.googleapis.com/css2?family=Montserrat:wght@600;700&family=Questrial&display=swap">
<style>
  :root{
    --blue:#3f86e8;
    --blue-deep:#2f73d6;
    --ink:#1c1c1c;
    --white:#ffffff;
    --page:#e9ecf0;
    --tile-a:#d9cbb8;
    --tile-b:#8d8f96;
    --tile-c:#e8d6bd;
    --tile-d:#eceae6;
    --tile-e:#d9d7d3;
    --tile-f:#d8a57a;
  }
  *{margin:0;padding:0;box-sizing:border-box}
  html,body{width:1200px;height:900px;overflow:hidden;background:var(--page)}
  .canvas{width:1200px;height:900px;display:flex;flex-direction:column;align-items:center;justify-content:center;gap:48px}
  .card{width:640px;height:366px;border-radius:14px;position:relative;overflow:hidden;box-shadow:0 8px 24px rgba(0,0,0,.18)}

  /* back side */
  .card-back{background:var(--blue);color:var(--white);font-family:"Questrial",sans-serif}
  .back-title{position:absolute;top:30px;left:0;right:0;text-align:center;font-size:30px;letter-spacing:3px;text-transform:uppercase}
  .back-claim{position:absolute;top:78px;left:0;right:0;text-align:center;font-family:"Montserrat",sans-serif;font-weight:700;font-size:14px;letter-spacing:.5px;text-transform:uppercase}
  .services{position:absolute;top:118px;left:40px;right:40px;display:grid;grid-template-columns:repeat(3,1fr);gap:14px 28px}
  .service{display:flex;flex-direction:column;align-items:center;gap:6px}
  .service-photo{width:150px;height:82px;border:3px solid var(--white);border-radius:4px}
  .service-name{font-family:"Montserrat",sans-serif;font-weight:600;font-size:12px;text-align:center;line-height:1.2}
  .painting{background:linear-gradient(135deg,#3b3b3b,#c9744a 45%,#e3c24e 70%,#4b6fb0)}
  .flooring{background:linear-gradient(135deg,var(--tile-a),var(--tile-b))}
  .kitchens{background:linear-gradient(135deg,#f3eee5,var(--tile-c))}
  .bathrooms{background:linear-gradient(135deg,var(--tile-d),#cfdcd8)}
  .energy{background:linear-gradient(135deg,var(--tile-e),#9c9a97)}
  .custom{background:linear-gradient(135deg,#f1d9bf,var(--tile-f))}

  /* front side */
  .card-front{background:var(--white);font-family:"Questrial",sans-serif;color:var(--ink)}
  .front-wave{position:absolute;inset:0}
  .brand{position:absolute;left:60px;top:90px;width:230px;display:flex;align-items:center;gap:10px}
  .brand-mark{width:14px;height:14px;background:var(--ink);flex:none}
  .brand-name{font-size:22px;letter-spacing:1.5px;text-transform:uppercase;color:var(--ink);line-height:1.15}
  .divider{position:absolute;left:306px;top:66px;width:2px;height:120px;background:var(--blue)}
  .contact{position:absolute;left:328px;top:70px}
  .person-name{font-family:"Montserrat",sans-serif;font-weight:700;font-size:28px;color:var(--blue);text-transform:uppercase;letter-spacing:.5px}
  .person-role{font-size:19px;margin-top:2px}
  .contact-line{display:flex;align-items:center;gap:8px;font-size:18px;margin-top:8px}
  .contact-line svg{width:14px;height:14px;flex:none}
</style>
</head>
<body>
<main class="canvas">

  <section class="card card-back" aria-label="Back of business card">
    <h2 class="back-title">Harborline Builders</h2>
    <p class="back-claim">Our services are 100% guaranteed</p>
    <ul class="services">
      <li class="service"><div class="service-photo painting" role="img" aria-label="Photo of open paint cans and brushes"></div><span class="service-name">Painting</span></li>
      <li class="service"><div class="service-photo flooring" role="img" aria-label="Photo of flooring samples"></div><span class="service-name">Flooring</span></li>
      <li class="service"><div class="service-photo kitchens" role="img" aria-label="Photo of a renovated kitchen"></div><span class="service-name">Kitchens</span></li>
      <li class="service"><div class="service-photo bathrooms" role="img" aria-label="Photo of a bright bathroom"></div><span class="service-name">Bathrooms</span></li>
      <li class="service"><div class="service-photo energy" role="img" aria-label="Photo of a modern energy efficient interior"></div><span class="service-name">Energy Efficient<br>Upgrades</span></li>
      <li class="service"><div class="service-photo custom" role="img" aria-label="Photo of a custom wood renovation"></div><span class="service-name">Custom Renovations</span></li>
    </ul>
  </section>

  <section class="card card-front" aria-label="Front of business card">
    <svg class="front-wave" viewBox="0 0 640 366" preserveAspectRatio="none" aria-hidden="true">
      <path d="M0 210 C120 330 330 352 640 352 L640 366 L0 366 Z" fill="var(--blue)"/>
      <path d="M0 238 C140 335 330 346 640 340" fill="none" stroke="var(--ink)" stroke-width="4"/>
      <path d="M0 250 C150 340 340 352 640 346 L640 366 L0 366 Z" fill="var(--blue)"/>
    </svg>
    <div class="brand">
      <span class="brand-mark"></span>
      <span class="brand-name">Harborline Builders</span>
    </div>
    <div class="divider"></div>
    <div class="contact">
      <h1 class="person-name">Marcus Delling</h1>
      <p class="person-role">Licensed General Contractors</p>
      <p class="contact-line">
        <svg viewBox="0 0 24 24"><path fill="var(--blue)" d="M6.6 10.8a15 15 0 0 0 6.6 6.6l2.2-2.2c.3-.3.7-.4 1-.2 1.1.4 2.3.6 3.6.6.6 0 1 .4 1 1V20c0 .6-.4 1-1 1A17 17 0 0 1 3 4c0-.6.4-1 1-1h3.5c.6 0 1 .4 1 1 0 1.3.2 2.5.6 3.6.1.3 0 .7-.2 1z"/></svg>
        858-471-6093
      </p>
      <p class="contact-line">
        <svg viewBox="0 0 24 24"><circle cx="12" cy="12" r="10" fill="var(--blue)"/><path d="M2 12h20M12 2c3 3 3 17 0 20M12 2c-3 3-3 17 0 20" stroke="var(--white)" stroke-width="1.5" fill="none"/></svg>
        www.brightoakbuilders.com
      </p>
    </div>
  </section>

</main>
</body>
</html>
```